Etikett für einen Rosé Wein
Zielgruppe
Wir sind ein Weingut und benötigen ein neues Etikett für unseren Muskattrollinger Rosé. Unsere Kunden sind eher traditionelle Weinkäufer.
Aufgabenstellung
Format:
Höhe: 9 cm
Breite: 11 cm
Da es nur ein Vorderetikett gibt, müssen alle relevanten Angaben (Hersteller, Alkohol, Inhalt in L, Rebsorte, etc.) enthalten sein. (siehe Flaschenabbildung anbei)
WÜRTTEMBERG
2019er
Muskattrollinger Rosé
DEUTSCHER QUALITÄTSWEIN
11,0 % Vol.
0,75 l
Enthält Sulfite
A.P.Nr. 58127364
Abfüller
Straße / PLZ / Ort / Tel.
Der Flaschenverschluss ist schwarz d.h. das neue Etikettendesign sollte dazu passen.
Bisher ist der Hintergrund des Weinetiketts schwarz. Dies muss jedoch nicht so bleiben.
Im Anhang finden Sie außerdem ein Plakat. Ggf. können Sie für das Flaschendesign einige nostalgische Elemente davon übernehmen.

```html
<!DOCTYPE html>
<html lang="de">
<head>
<meta charset="utf-8">
<title>Muskattrollinger Rosé – Etikett</title>
<link href="https://fonts.googleapis.com/css2?family=EB+Garamond:wght@500;600;700&family=Allura&display=swap" rel="stylesheet">
<style>
  :root {
    --page-bg: #2e231d;
    --label-bg: #2a2a2b;
    --label-bg-light: #363637;
    --accent: #c9461c;
    --ink: #f4f1ec;
    --art-light: #9a9a9a;
    --art-dark: #3c3c3c;
  }
  * { margin: 0; padding: 0; box-sizing: border-box; }
  html, body {
    width: 1100px; height: 1200px; overflow: hidden;
    background: var(--page-bg);
  }
  .label {
    position: absolute; left: 50px; top: 191px;
    width: 1000px; height: 818px;
    background: radial-gradient(ellipse at 40% 35%, var(--label-bg-light), var(--label-bg) 70%);
    box-shadow: 0 6px 18px rgba(0,0,0,.45);
    font-family: "EB Garamond", Georgia, serif;
    color: var(--ink);
  }
  .label > * { position: absolute; white-space: nowrap; }
  .region {
    left: 249px; width: 502px; top: 28px;
    font-size: 88px; font-weight: 700; letter-spacing: 2px;
    color: var(--accent); text-align: center; line-height: 1;
  }
  .vintage {
    right: 249px; top: 112px; font-size: 32px; font-weight: 500; line-height: 1;
  }
  .variety, .style {
    font-family: "Allura", cursive; color: var(--ink); line-height: 1;
  }
  .variety { left: 248px; top: 168px; font-size: 112px; }
  .style { left: 518px; top: 272px; font-size: 120px; }
  .grape-art {
    left: 176px; top: 265px; width: 273px; height: 380px;
    background: radial-gradient(ellipse at 55% 60%, var(--art-light), var(--art-dark) 75%, transparent 100%);
    opacity: .8; border-radius: 45% 45% 50% 50%;
  }
  .quality {
    right: 302px; top: 452px; text-align: right;
    color: var(--accent); font-size: 27px; font-weight: 500;
    letter-spacing: 1px; line-height: 45px;
  }
  .legal {
    right: 302px; top: 574px; text-align: right;
    font-size: 24px; font-weight: 600; line-height: 38px;
  }
  .legal .marketer { color: var(--accent); font-weight: 500; font-size: 22px; }
  .alcohol {
    left: 78px; top: 616px; font-size: 27px; font-weight: 600; line-height: 38px;
  }
  .alcohol .allergen { display: block; color: var(--accent); font-size: 21px; font-weight: 500; }
  .volume { right: 80px; top: 640px; font-size: 36px; font-weight: 600; }
  .address {
    left: 0; width: 100%; top: 748px; text-align: center;
    font-size: 23px; font-weight: 600;
  }
  .address .dot { color: var(--accent); padding: 0 6px; }
</style>
</head>
<body>
  <main class="label">
    <div class="grape-art" role="img" aria-label="Gravierte Illustration einer Weintraube mit Rebblatt"></div>
    <h1 class="region">Württemberg</h1>
    <div class="vintage">2019 er</div>
    <div class="variety">Muskattrollinger</div>
    <div class="style">Rosé</div>
    <div class="quality">DEUTSCHER<br>QUALITÄTSWEIN</div>
    <div class="legal">
      A.P.Nr. 581 273 64<br>
      Abfüller D-BWW 517<br>
      <span class="marketer">vermarkted durch: Lukas Renner</span>
    </div>
    <div class="alcohol">11,0% Vol.<span class="allergen">Enthalten Sulfit</span></div>
    <div class="volume">0,75 l</div>
    <div class="address">Straße 5<span class="dot">•</span>D-71580 Talbach - Steinweiler<span class="dot">•</span>Tel. 071 44/5093817</div>
  </main>
</body>
</html>
```